Bluecrest Learning Corps by graduating students from college in two years

Based on the logo design, create stationary and business cards for
Dr. Venrel T Oskamp, CEO, (703) 482-1736
and Marisa Deltoft, Respresentative, (301) 647-2208
Address: 4719 Pellham Court, Brinmore Station, VA 20417
Incorporate elelments of the logo

Target Market(s)

USA

Font styles to use
Other font styles liked:
• match with the logo type style

```html
<!DOCTYPE html>
<html lang="en">
<head>
<meta charset="utf-8">
<title>Bluecrest Learning Corps Letterhead</title>
<link href="https://fonts.googleapis.com/css2?family=Arimo:wght@400;700&family=Questrial&display=swap" rel="stylesheet">
<style>
  :root {
    --navy: #1b2a6b;
    --gold: #f2b632;
    --ink: #4a4a4a;
    --muted: #5a5a5a;
    --rule: #8a8a8a;
    --paper: #ffffff;
    --backdrop: #d6d6d6;
    --motif: #eef0f5;
  }
  * { box-sizing: border-box; margin: 0; padding: 0; }
  html, body { width: 1200px; height: 1159px; overflow: hidden; }
  body {
    background: var(--backdrop);
    font-family: "Arimo", Arial, sans-serif;
    color: var(--ink);
    display: flex; align-items: center; justify-content: center;
  }
  .letterhead {
    position: relative;
    width: 790px; height: 1110px;
    background: var(--paper);
    box-shadow: 0 4px 18px rgba(0,0,0,.18);
    padding: 56px 40px 0 40px;
    overflow: hidden;
  }
  .masthead { position: relative; z-index: 1; display: flex; align-items: center; height: 150px; }
  .brand { display: flex; align-items: center; gap: 12px; width: 196px; flex: none; }
  .brand-dot { width: 44px; height: 44px; border-radius: 50%; background: var(--gold); flex: none; }
  .brand-name { font-weight: 700; font-size: 16px; line-height: 1.2; color: var(--navy); }
  .masthead-rules {
    flex: 1; height: 104px;
    border-top: 1px solid var(--rule); border-bottom: 1px solid var(--rule);
    display: flex; align-items: center; justify-content: space-between; padding: 0 4px 0 14px;
  }
  .contact { padding: 4px 16px; font-size: 12.5px; line-height: 1.4; white-space: nowrap; }
  .contact + .contact { border-left: 1px solid var(--gold); }
  .contact-name { font-weight: 700; font-size: 14px; color: var(--navy); }
  .contact-role { color: var(--muted); }
  .contact-phone { display: flex; align-items: center; gap: 5px; color: var(--muted); }
  .contact-phone svg { width: 11px; height: 11px; fill: var(--gold); flex: none; }
  .address { color: #666; }
  .letter { position: relative; z-index: 1; padding: 200px 40px 0 150px; font-size: 13.5px; line-height: 1.3; }
  .salutation { font-family: "Questrial", sans-serif; font-weight: 700; font-size: 19px; color: var(--muted); margin-bottom: 26px; }
  .letter p { margin-bottom: 22px; }
  .closing { font-family: "Questrial", sans-serif; font-weight: 700; font-size: 12px; margin-top: 40px; }
  .signature { width: 150px; height: 38px; margin-top: 22px; background: linear-gradient(90deg, #e6e6e6, #f2f2f2); border-radius: 4px; }
  .watermark {
    position: absolute; right: 0; bottom: 0;
    width: 420px; height: 420px;
    background: radial-gradient(circle at 70% 70%, var(--motif) 0%, rgba(238,240,245,.6) 55%, rgba(255,255,255,0) 75%);
  }
</style>
</head>
<body>
  <main class="letterhead">
    <div class="watermark" role="img" aria-label="Faint decorative graduation motif"></div>
    <header class="masthead">
      <div class="brand">
        <span class="brand-dot"></span>
        <span class="brand-name">Bluecrest Learning Corps</span>
      </div>
      <div class="masthead-rules">
        <div class="contact">
          <div class="contact-name">Dr. Venrel T Oskamp</div>
          <div class="contact-role">CEO</div>
          <div class="contact-phone"><svg viewBox="0 0 24 24"><path d="M6.6 10.8a15 15 0 0 0 6.6 6.6l2.2-2.2a1 1 0 0 1 1-.25 11.4 11.4 0 0 0 3.6.57 1 1 0 0 1 1 1V20a1 1 0 0 1-1 1A17 17 0 0 1 3 4a1 1 0 0 1 1-1h3.5a1 1 0 0 1 1 1c0 1.25.2 2.45.57 3.57a1 1 0 0 1-.25 1z"/></svg>(703) 482-1736</div>
        </div>
        <div class="contact">
          <div class="contact-name">Marisa Deltoft</div>
          <div class="contact-role">Respresentative</div>
          <div class="contact-phone"><svg viewBox="0 0 24 24"><path d="M6.6 10.8a15 15 0 0 0 6.6 6.6l2.2-2.2a1 1 0 0 1 1-.25 11.4 11.4 0 0 0 3.6.57 1 1 0 0 1 1 1V20a1 1 0 0 1-1 1A17 17 0 0 1 3 4a1 1 0 0 1 1-1h3.5a1 1 0 0 1 1 1c0 1.25.2 2.45.57 3.57a1 1 0 0 1-.25 1z"/></svg>(301) 647-2208</div>
        </div>
        <div class="contact address">
          4719 Pellham Court<br>Brinmore Station<br>VA 20417
        </div>
      </div>
    </header>

    <section class="letter">
      <h1 class="salutation">Dear Mr. Smith,</h1>
      <p>Lorem ipsum dolor sit amet, consectetuer adipiscing elit, sed diam nonmmy nibh euismod tincidunt ut laor eet dolore magna aliquam erat volutpat. Ut wisi enim ad minim veniam, quis nostrud exerci tationmcorper suscipit lobortis nisl ut aliquip ex ea commodo consequat. Duis autem vel eum iriure dolor in hendrerit in vulputate velit esse molestie consequat, vel illum dolore eu feugiat</p>
      <p>Rorem ipsum dolor sit amet, consectetuer adipiscing elit, sed diam nonmmy nibh euismod tincidunt ut laor eet dolore magna aliquam erat volutpat. Ut wisi enim ad minim veniam, quis nostrud exerci tationmcorper suscipit lobortis nisl ut aliquip ex ea commodo consequat. Duis autem vel eum iriure dolor in hendrerit in vulputate velit esse molest</p>
      <p>Dorem ipsum dolor sit amet, consectetuer adipiscing elit, sed diam nonmmy nibh euismod tincidunt ut laor eet dolore magna aliquam erat volutpat. Ut wisi enim ad minim veniam, quis nostrud exerci tationmcorper suscipit lobortis nisl ut aliquip ex ea commodo consequat. Duis autem vel eum iriure dolor in hendrerit in suscipit lobortis nisl ut aliquip ex ea commodo consequat. Duis autem vel eum iriure dolor in hendrerit in vulputate velit esse molestie consequat, vel illum</p>
      <p>Sorem ipsum dolor sit amet, consectetuer adipiscing elit, sed diam nonmmy nibh euismod tincidunt ut laor eet dolore magna aliquam erat volutpat. Ut wisi enim ad minim veniam, quis nostrud exerci tationmcorper suscipit lobortis nisl ut aliquip ex ea commodo consequat. Duis autem vel eum iriure dolor in</p>
      <div class="closing">Sincerely,</div>
      <div class="signature" role="img" aria-label="Handwritten signature"></div>
    </section>
  </main>
</body>
</html>
```